Home Remodeling company needs a business card design

we need a business card design for home remodeling company in hamilton county, indiana USA. we offers a wide range of construction services including whole house renovations, Design and Build Basements and Kitchen and Bathroom Remodeling . we would like to see designs for both site of business card that use the same color of the company logo and also including all information below :
1- Karim Feltous CEO / General Contractor
2- all company contacts Telephone numbers ( 1-888-DULOM-47 ) ( 317-555-0193) email address ( info@dulomhome.com) website ( www.dulomhome.com ) and social media logos (Facebook- twitter- google plus )
3- company logo
4- licensed . insured . bonded

```html
<!DOCTYPE html>
<html lang="en">
<head>
<meta charset="utf-8">
<title>Dulom Home Remodeling – Business Card</title>
<link rel="stylesheet" href="https://fonts.googleapis.com/css2?family=Lato:ital,wght@0,400;0,700;0,900;1,400&display=swap">
<style>
  :root {
    --backdrop: #8e8e8e;
    --paper: #f2f2f2;
    --brand-red: #a8282f;
    --ink-dark: #2f2f30;
    --ink-mid: #555558;
    --rule-grey: #9a9a9a;
    --band-dark: #2b2b2c;
    --white: #ffffff;
  }
  * { box-sizing: border-box; margin: 0; padding: 0; }
  html, body {
    width: 1105px; height: 1200px; overflow: hidden;
    background: var(--backdrop);
    font-family: "Lato", Arial, sans-serif;
  }
  .card {
    position: absolute; left: 178px; width: 748px; height: 427px;
    overflow: hidden;
  }
  .card--front { top: 119px; background: var(--paper); }
  .card--back { top: 637px; background: var(--brand-red); }

  /* brand lockup */
  .brand { position: absolute; }
  .brand__row { display: flex; align-items: center; gap: 12px; }
  .brand__square { width: 14px; height: 14px; background: var(--brand-red); }
  .brand__name { font-weight: 900; line-height: 1; letter-spacing: 2px; }
  .brand__tagline { font-weight: 400; letter-spacing: 5.4px; line-height: 1; margin-top: 8px; }

  .card--front .brand { right: 46px; top: 40px; }
  .card--front .brand__name { font-size: 60px; color: var(--ink-dark); }
  .card--front .brand__tagline { font-size: 17px; color: var(--ink-mid); padding-left: 26px; }

  .card--back .brand { left: 50%; top: 168px; transform: translateX(-50%); }
  .card--back .brand__square { background: var(--white); }
  .card--back .brand__name { font-size: 68px; color: var(--white); }
  .card--back .brand__tagline { font-size: 19px; color: var(--white); padding-left: 26px; }

  /* person */
  .person { position: absolute; left: 44px; top: 198px; }
  .person__name { font-size: 25px; font-weight: 700; color: var(--ink-dark); }
  .person__role { font-size: 19px; color: var(--brand-red); margin-top: 6px; }
  .divider { position: absolute; left: 44px; top: 263px; width: 660px; height: 2px; background: var(--rule-grey); }

  .contacts { position: absolute; left: 44px; top: 280px; list-style: none; }
  .contacts li {
    display: flex; align-items: center; gap: 12px;
    height: 28px; font-size: 18px; color: var(--ink-dark);
  }
  .contacts svg { width: 16px; height: 16px; fill: var(--ink-dark); }

  .credentials {
    position: absolute; right: 44px; top: 307px; text-align: right;
    font-size: 19px; color: var(--brand-red); line-height: 29px; letter-spacing: 0.3px;
  }

  .footer-strip { position: absolute; left: 0; bottom: 0; width: 748px; height: 43px; }
  .website {
    position: absolute; right: 34px; bottom: 10px;
    font-size: 17px; font-style: italic; color: var(--white); letter-spacing: 2.6px;
  }

  .social { position: absolute; left: 50%; top: 360px; transform: translateX(-50%); display: flex; align-items: center; gap: 6px; }
  .social__line { width: 50px; height: 1px; background: rgba(255,255,255,0.6); }
  .social__dot { width: 25px; height: 25px; border-radius: 50%; background: var(--white); }
</style>
</head>
<body>

<section class="card card--front" aria-label="Business card front">
  <div class="brand">
    <div class="brand__row">
      <span class="brand__square"></span>
      <span class="brand__name">DULOM</span>
    </div>
    <div class="brand__tagline">HOME REMODELING</div>
  </div>

  <div class="person">
    <div class="person__name">Karim Feltous</div>
    <div class="person__role">CEO / General Contractor</div>
  </div>
  <div class="divider"></div>

  <ul class="contacts">
    <li>
      <svg viewBox="0 0 16 16" aria-hidden="true"><path d="M3.5 1.2l2.2 2.9c.3.4.2.9-.1 1.2L4.5 6.4c.9 2 2.6 3.7 4.6 4.6l1.1-1.1c.3-.3.8-.4 1.2-.1l2.9 2.2c.4.3.4.9.1 1.2l-1.3 1.4c-.6.6-1.5.8-2.3.5C6.5 13.6 2.4 9.5.9 5.1.6 4.3.8 3.4 1.4 2.8L2.3 1.1c.3-.3.9-.3 1.2.1z"/></svg>
      <span>1-888-DULOM-47</span>
    </li>
    <li>
      <svg viewBox="0 0 16 16" aria-hidden="true"><path d="M4.5 0h7A1.5 1.5 0 0 1 13 1.5v13a1.5 1.5 0 0 1-1.5 1.5h-7A1.5 1.5 0 0 1 3 14.5v-13A1.5 1.5 0 0 1 4.5 0zm.3 2v10.5h6.4V2zM8 13.3a.9.9 0 1 0 0 1.8.9.9 0 0 0 0-1.8z"/></svg>
      <span>317-555-0193</span>
    </li>
    <li>
      <svg viewBox="0 0 16 16" aria-hidden="true"><path d="M1 3h14v1.2L8 8.6 1 4.2zm0 2.6l7 4.4 7-4.4V13H1z"/></svg>
      <span>info@dulomhome.com</span>
    </li>
  </ul>

  <div class="credentials">LICENSED<br>INSURED | BONDED</div>

  <svg class="footer-strip" viewBox="0 0 748 43" aria-hidden="true">
    <rect x="0" y="16" width="440" height="3" fill="var(--rule-grey)"/>
    <polygon points="0,19 440,19 436,25 0,25" fill="var(--brand-red)"/>
    <polygon points="447,0 748,0 748,43 431,43" fill="var(--band-dark)"/>
  </svg>
  <div class="website">www.dulomhome.com</div>
</section>

<section class="card card--back" aria-label="Business card back">
  <div class="brand">
    <div class="brand__row">
      <span class="brand__square"></span>
      <span class="brand__name">DULOM</span>
    </div>
    <div class="brand__tagline">HOME REMODELING</div>
  </div>

  <div class="social" aria-label="Social media links">
    <span class="social__line"></span>
    <span class="social__dot"></span>
    <span class="social__dot"></span>
    <span class="social__dot"></span>
    <span class="social__line"></span>
  </div>
</section>

</body>
</html>
```